Podiatry clinic requires a modern revamp and editing of existing website.

I would like a fresh new look and updated information for my current business website. An easy to navigate site with prominent address and phone number for call to action. We are a podiatry clinic that focuses on general and sports podiatry.
I would like 4 pages; including Home page, About Us, Services & Contact.
www.brambleridgepodiatry.net

Target Market(s)

Active working professionals.

Industry/Entity Type

Medical

Coding

Coded - Design and coding required

Number of Pages Required

4 page

Font styles to use
Sans Serif

Colors
6b449b

Requirements
Must have
• A modern look with logo and active images; clean and uncluttered. Visible phone number and address for call to action.
• 4 pages - Home, About Us, Services, Contact.
• Home page - update address & service logos.
• About Us - update of personal information.
• Services - Revamp of existing page.
• Contact page to include Google map, email & phone number.
Nice to have
• Ability to add content easily; eg. a blog or adding video onto Home page.
• Link to Social page page.

```html
<!DOCTYPE html>
<html lang="en">
<head>
<meta charset="utf-8">
<title>Bramble Ridge Podiatry</title>
<link href="https://fonts.googleapis.com/css2?family=Raleway:wght@300;400;500;600;700;800&family=Open+Sans:wght@400;600;700&display=swap" rel="stylesheet">
<style>
:root{
  --purple:#54379a;
  --purple-dark:#45298a;
  --green:#7cc243;
  --orange:#ef7d22;
  --ink:#4a4a4a;
  --muted:#6a6a6a;
  --light:#f0f0f0;
  --white:#ffffff;
  --skin:#eebfa3;
  --skin-deep:#d89a7c;
  --sea:#2f4f9e;
}
*{box-sizing:border-box;margin:0;padding:0}
html,body{width:1200px;height:3103px;overflow:hidden}
body{font-family:"Open Sans",Arial,sans-serif;color:var(--ink);background:var(--white);position:relative}

/* hero */
.hero{position:absolute;left:0;top:0;width:1200px;height:800px;overflow:hidden}
.hero-photo{position:absolute;inset:0;
  background:
    radial-gradient(ellipse 340px 520px at 1000px 260px,rgba(238,191,163,.75),rgba(238,191,163,0) 70%),
    radial-gradient(ellipse 420px 160px at 230px 330px,rgba(255,255,255,.35),rgba(255,255,255,0) 70%),
    linear-gradient(180deg,#f6f2f8 0%,#e6e0f0 16%,#b9bfe0 34%,#7f95cf 50%,#2f5aa8 58%,#2c4c9c 70%,#3e3ca0 84%,#5a38a6 100%)}
.hero-top{position:absolute;left:78px;right:78px;top:30px;display:flex;justify-content:space-between;
  padding-bottom:22px;border-bottom:1px solid rgba(84,55,154,.25)}
.hero-address{display:flex;gap:10px;color:var(--purple);font-size:20px;line-height:1.25}
.hero-call{display:flex;align-items:center;gap:14px;color:var(--purple)}
.hero-call small{display:block;font-size:16px;text-transform:uppercase}
.hero-call strong{display:block;font-size:30px;font-weight:700;line-height:1.1}
.brand{position:absolute;left:420px;top:150px;display:flex;align-items:center;gap:22px}
.brand-mark{width:96px;height:96px;border-radius:50%;background:var(--purple);flex:none}
.brand-name{font-family:"Raleway",Arial,sans-serif;font-weight:700;font-size:56px;color:var(--white);line-height:1.12;width:380px}
.hero-title{position:absolute;left:0;right:0;top:425px;text-align:center;color:var(--white);
  font-family:"Raleway",Arial,sans-serif;font-weight:800;font-size:48px;line-height:62px;text-transform:uppercase}
.btn{display:inline-block;background:var(--purple);color:var(--white);font-family:"Raleway",Arial,sans-serif;
  text-transform:uppercase;border-radius:32px;text-align:center}
.hero .btn{position:absolute;left:486px;top:578px;width:228px;height:64px;line-height:64px;font-size:26px}

/* navigation */
.nav{position:absolute;left:0;top:800px;width:1200px;height:62px;background:var(--purple-dark);display:flex;padding-left:78px}
.nav a{color:var(--white);text-decoration:none;font-size:18px;line-height:62px;padding:0 38px;text-transform:uppercase}
.nav a.active{background:var(--green);padding:0 32px}

/* welcome */
.welcome{position:absolute;left:0;top:910px;width:1200px;text-align:center}
.section-title{font-family:"Raleway",Arial,sans-serif;font-weight:400;font-size:42px;color:var(--ink);text-transform:uppercase}
.section-title span{color:var(--purple)}
.welcome p{font-size:15.5px;line-height:26px;color:var(--muted);width:840px;margin:22px auto 0}
.welcome .btn{margin-top:28px;width:190px;height:50px;line-height:50px;font-size:24px}

/* appointments */
.appoint{position:absolute;left:78px;top:1233px;width:1044px;height:256px;background:var(--light);
  border-bottom:5px solid var(--purple);box-shadow:0 26px 30px -18px rgba(0,0,0,.35);text-align:center;overflow:hidden}
.appoint-dot{position:absolute;left:72px;top:60px;width:110px;height:110px;border-radius:50%;background:#d6d6d6}
.appoint-photo{position:absolute;right:0;top:0;width:200px;height:251px;
  background:radial-gradient(ellipse 80px 130px at 130px 130px,var(--skin) 0%,var(--skin-deep) 45%,rgba(240,240,240,0) 100%)}
.appoint h2{font-family:"Raleway",Arial,sans-serif;font-weight:400;font-size:40px;color:var(--orange);margin-top:24px}
.appoint .call{display:flex;justify-content:center;align-items:center;gap:12px;margin-top:12px;font-family:"Raleway",Arial,sans-serif;font-size:31px;color:var(--green)}
.appoint .call strong{font-weight:700}
.appoint .or{font-size:19px;color:var(--muted);margin-top:14px}
.appoint .mail{font-size:20px;color:var(--purple);margin-top:10px;display:flex;justify-content:center;gap:8px;align-items:center}

/* services */
.services{position:absolute;left:0;top:1560px;width:1200px}
.services .section-title{text-align:center}
.service-list{display:flex;gap:39px;padding-left:78px;margin-top:30px}
.service{width:322px}
.service-photo{height:197px}
.photo-general{background:
  radial-gradient(ellipse 110px 90px at 190px 120px,#f0cdb6,rgba(240,205,182,0) 80%),
  linear-gradient(120deg,#b9c4cf 0%,#eef1f4 40%,#f4f4f4 60%,#c9d2da 100%)}
.photo-special{background:
  radial-gradient(ellipse 90px 100px at 140px 80px,#f2d9c8,rgba(242,217,200,0) 85%),
  linear-gradient(180deg,#eef0ee 0%,#e8e4de 55%,#6fb3a0 80%,#3f8f83 100%)}
.photo-sports{background:
  radial-gradient(ellipse 60px 80px at 60px 90px,#3f74c0,rgba(63,116,192,0) 90%),
  radial-gradient(ellipse 90px 70px at 220px 120px,#e9c2a6,rgba(233,194,166,0) 90%),
  linear-gradient(135deg,#5a3a26,#8a5c40 50%,#6a4530)}
.service h3{font-family:"Raleway",Arial,sans-serif;font-weight:400;font-size:27px;color:var(--purple);margin-top:14px}
.service p{font-size:15px;line-height:26px;color:var(--muted);margin-top:8px;height:80px}
.more{display:inline-flex;align-items:center;gap:6px;font-weight:700;font-size:17px;color:var(--purple-dark);text-transform:uppercase;margin-top:6px}

/* follow */
.follow{position:absolute;left:0;top:2078px;width:1200px;height:252px;background:var(--light)}
.follow-photo{position:absolute;left:40px;top:0;width:340px;height:240px;
  background:radial-gradient(ellipse 170px 110px at 170px 110px,var(--skin) 0%,#e8b79c 45%,rgba(240,240,240,0) 100%)}
.follow .section-title{position:absolute;left:0;right:0;top:28px;text-align:center}
.follow-card{position:absolute;left:408px;top:98px;display:flex;gap:20px;align-items:center}
.follow-badge{width:124px;height:124px;border-radius:50%;background:var(--white);border:1px solid #ddd}
.follow-card h4{font-weight:400;font-size:22px;color:var(--purple)}
.like{display:inline-block;margin-top:8px;padding:6px 20px;border:2px solid var(--purple);border-radius:4px;background:#e4e8f2;
  color:#2f4c8f;font-weight:700;font-size:21px;line-height:25px}

/* partners */
.partners{position:absolute;left:0;top:2330px;width:1200px;height:168px;display:flex;justify-content:space-between;align-items:center;padding:0 78px}
.partner{height:84px;border-radius:8px}
.p1{width:232px;background:linear-gradient(90deg,#f5c542 0 22%,#2d3f8f 22%)}
.p2{width:212px;background:linear-gradient(90deg,#2a62b0 0 30%,#e3e9f5 30%)}
.p3{width:216px;background:linear-gradient(90deg,#d9ecd2 0 22%,#1fa243 22%)}
.p4{width:234px;background:#2a2a2a}

/* contact */
.contact{position:absolute;left:0;top:2498px;width:1200px;height:552px;
  background:
    radial-gradient(ellipse 140px 300px at 1000px 330px,rgba(70,60,120,.65),rgba(70,60,120,0) 80%),
    linear-gradient(180deg,#3f3e32 0%,#6e6b52 30%,#5a563f 60%,#3a352b 85%,#26221d 100%)}
.contact .section-title{position:absolute;left:0;right:0;top:48px;text-align:center;color:var(--white)}
.form{position:absolute;left:78px;top:160px;width:436px}
.field{background:var(--white);border-radius:4px;height:50px;margin-bottom:8px;padding:14px 20px;font-size:14px;color:#9a9a9a}
.field.message{height:104px}
.form .btn{width:164px;height:50px;line-height:50px;font-size:22px;font-weight:700;margin-top:8px}
.map{position:absolute;left:534px;top:160px;width:276px;height:276px;
  background:linear-gradient(125deg,#ecebe6 0%,#e2e0d9 45%,#f1efea 55%,#e6e4dd 100%)}
.address{position:absolute;left:852px;top:160px;color:var(--white)}
.address h4{font-family:"Raleway",Arial,sans-serif;font-weight:500;font-size:21px;text-transform:uppercase}
.address li{list-style:none;display:flex;gap:14px;font-size:15.5px;line-height:24px;margin-top:18px}
.social{display:flex;gap:14px;margin-top:24px}
.social i{display:block;width:46px;height:46px;border:2px solid var(--white);border-radius:50%}
.social i:first-child{background:var(--white)}

.footer{position:absolute;left:0;top:3050px;width:1200px;height:53px;background:var(--purple);color:var(--white);
  text-align:center;line-height:53px;font-size:15px}
</style>
</head>
<body>

<header class="hero">
  <div class="hero-photo" role="img" aria-label="Bare feet resting on a boat rail above a blue sea"></div>
  <div class="hero-top">
    <div class="hero-address">
      <svg width="20" height="26" viewBox="0 0 20 26"><path d="M10 1a8 8 0 0 0-8 8c0 6 8 16 8 16s8-10 8-16a8 8 0 0 0-8-8z" fill="var(--purple)"/><circle cx="10" cy="9" r="3" fill="#fff"/></svg>
      <div>Suite 214 / 77 Larkin<br>Street Eastbourne 3100</div>
    </div>
    <div class="hero-call">
      <svg width="48" height="48" viewBox="0 0 48 48"><circle cx="24" cy="24" r="22" fill="none" stroke="var(--purple)" stroke-width="2.5"/><path d="M17 14l5 0 2 6-3 2c1 3 3 5 6 6l2-3 6 2v5c-9 1-19-8-18-18z" fill="var(--purple)"/></svg>
      <div><small>Call us now!</small><strong>1300 555 208</strong></div>
    </div>
  </div>
  <div class="brand">
    <span class="brand-mark"></span>
    <span class="brand-name">Bramble Ridge Podiatry</span>
  </div>
  <h1 class="hero-title">Don't let pain run<br>your life</h1>
  <a class="btn">Contact us</a>
</header>

<nav class="nav">
  <a class="active">Home</a><a>About</a><a>Services</a><a>Contact</a>
</nav>

<section class="welcome">
  <h2 class="section-title">Welcome to <span>Bramble Ridge Podiatry</span></h2>
  <p>Bramble Ridge Podiatry is a Podiatry clinic in the heart of Eastbourne CBD. We are located between Larkin &amp; Harrow Streets in the Harbourline Business Centre / Wattle Court Complex.</p>
  <p>Our podiatrists are fully qualified health professionals who are able to diagnose, treat, manage or help to prevent all medical conditions that affect the feet and lower limb.</p>
  <a class="btn">Read more</a>
</section>

<section class="appoint">
  <span class="appoint-dot"></span>
  <div class="appoint-photo" role="img" aria-label="Hands massaging a foot"></div>
  <h2>For Appointments or Enquiries</h2>
  <div class="call">Please call us on
    <svg width="42" height="42" viewBox="0 0 48 48"><circle cx="24" cy="24" r="22" fill="none" stroke="var(--green)" stroke-width="2.5"/><path d="M17 14l5 0 2 6-3 2c1 3 3 5 6 6l2-3 6 2v5c-9 1-19-8-18-18z" fill="var(--green)"/></svg>
    <strong>1300 555 208</strong></div>
  <div class="or">OR</div>
  <div class="mail">Email:
    <svg width="20" height="15" viewBox="0 0 20 15"><rect x="1" y="1" width="18" height="13" fill="none" stroke="var(--purple)" stroke-width="1.6"/><path d="M1 1l9 7 9-7" fill="none" stroke="var(--purple)" stroke-width="1.6"/></svg>
    info@brambleridgepodiatry.net</div>
</section>

<section class="services">
  <h2 class="section-title">Services <span>we provide</span></h2>
  <div class="service-list">
    <article class="service">
      <div class="service-photo photo-general" role="img" aria-label="Podiatrist examining a patient's foot"></div>
      <h3>General Treatment</h3>
      <p>Nails, Corns, Callus, Warts, Skin Disorders, Heel pain / Heel Spurs / Arch pain - plantar Fasciitis</p>
      <span class="more">Read more <svg width="14" height="12" viewBox="0 0 14 12"><path d="M1 1l5 5-5 5M7 1l5 5-5 5" fill="none" stroke="var(--purple-dark)" stroke-width="2"/></svg></span>
    </article>
    <article class="service">
      <div class="service-photo photo-special" role="img" aria-label="Gloved hands treating the sole of a foot"></div>
      <h3>Specialised Treatments</h3>
      <p>Diabetic Management, Nail Surgery, Biomechanical Assessment, Gait Analysis, Orthotic Therapy</p>
      <span class="more">Read more <svg width="14" height="12" viewBox="0 0 14 12"><path d="M1 1l5 5-5 5M7 1l5 5-5 5" fill="none" stroke="var(--purple-dark)" stroke-width="2"/></svg></span>
    </article>
    <article class="service">
      <div class="service-photo photo-sports" role="img" aria-label="Runner holding an injured ankle beside sports shoes"></div>
      <h3>Sports Injury</h3>
      <p>Podiatrists are trained to diagnose and treat all medical conditions that affect the feet and lower limb.</p>
      <span class="more">Read more <svg width="14" height="12" viewBox="0 0 14 12"><path d="M1 1l5 5-5 5M7 1l5 5-5 5" fill="none" stroke="var(--purple-dark)" stroke-width="2"/></svg></span>
    </article>
  </div>
</section>

<section class="follow">
  <div class="follow-photo" role="img" aria-label="Hands resting on bare feet"></div>
  <h2 class="section-title">Follow <span>us</span></h2>
  <div class="follow-card">
    <span class="follow-badge"></span>
    <div>
      <h4>Bramble Ridge Podiatry</h4>
      <span class="like">Like Us on<br>our page</span>
    </div>
  </div>
</section>

<section class="partners" aria-label="Associations and payment partners">
  <span class="partner p1"></span><span class="partner p2"></span><span class="partner p3"></span><span class="partner p4"></span>
</section>

<section class="contact">
  <h2 class="section-title">Contact us</h2>
  <div class="form">
    <div class="field">Name</div>
    <div class="field">E-Mail</div>
    <div class="field">Phone</div>
    <div class="field message">Message</div>
    <a class="btn">Submit</a>
  </div>
  <div class="map" role="img" aria-label="Street map showing the clinic location"></div>
  <div class="address">
    <h4>Contact address</h4>
    <ul>
      <li><svg width="20" height="26" viewBox="0 0 20 26"><path d="M10 1a8 8 0 0 0-8 8c0 6 8 16 8 16s8-10 8-16a8 8 0 0 0-8-8z" fill="none" stroke="#fff" stroke-width="1.6"/><circle cx="10" cy="9" r="3" fill="none" stroke="#fff" stroke-width="1.6"/></svg><span>Suite 214 / 77 Larkin Street<br>Eastbourne 3100.</span></li>
      <li><svg width="20" height="20" viewBox="0 0 20 20"><path d="M3 2h4l2 5-3 2c1 2 3 4 5 5l2-3 5 2v4C9 18 2 11 3 2z" fill="#fff"/></svg><strong>1300 555 208</strong></li>
      <li><svg width="20" height="15" viewBox="0 0 20 15"><rect x="1" y="1" width="18" height="13" fill="none" stroke="#fff" stroke-width="1.6"/><path d="M1 1l9 7 9-7" fill="none" stroke="#fff" stroke-width="1.6"/></svg>info@brambleridgepodiatry.net</li>
    </ul>
    <div class="social"><i></i><i></i><i></i></div>
  </div>
</section>

<footer class="footer">© Bramble Ridge Podiatry- 2016. All Rights Reserved.</footer>

</body>
</html>
```